Larkspur Talent IT Recruiting firm needs a business card design for Recruiters, Sourcers, and Account

We need business cards that allow us to change all contact info, names, titles (Recruiter, Sourcer, Account Manager, Director, CEO, etc) per person since we have three offices, in three cities, Phoenix, Austin, and Las Vegas. We do recruiting and contractors for IT positions (Developers, Architects, Software Engineers, Security Engineers, Help Desk, DBAs, PMs, Scrum Masters, etc.) Our client companies are very diverse from Meridian 100 to silicone Valley type start-ups.

So, while we what hip, techie, and quirky, it still needs to be professional. Primary color we use is blue, with silver as a secondary color.

Target Market(s)

IT, Technology

Industry/Entity Type

Business

Contact Information for Business Card

Company name: Larkspur Talent, Inc.
Website: www.larkspurtalent.example
Logos for Careerloop, Blipster, and Myriada

Name, Title, Office Number, Cell Number, email

Font styles to use
Serif
Sans Serif

Colors
0455a3
d5d5d5

Requirements
Nice to have
• The grey I selected below is not necessary - but, would like silver included. I included a card design (File 3: LTI early trial example.jpg) that I had started on. It's very rough, and not quite what we're looking for, but what we did like is the logo, big, maybe a bit faded, off center, goes out of frame, etc. Still looking for other ideas - you are the pros! But, just an idea of a design element we liked.

```html
<!DOCTYPE html>
<html lang="en">
<head>
<meta charset="utf-8">
<title>Larkspur Talent — Business Card</title>
<link rel="stylesheet" href="https://fonts.googleapis.com/css2?family=Cinzel:wght@400;600&family=Open+Sans:wght@400;700&display=swap">
<style>
  :root {
    --backdrop: #3a3a3c;
    --card: #111214;
    --card-edge: #1c1d20;
    --ink: #f2f2f2;
    --silver: #d5d5d5;
    --blue: #0455a3;
    --blue-bright: #2f8fe0;
    --blue-light: #6cc0f0;
    --faint: rgba(255,255,255,0.035);
  }
  * { box-sizing: border-box; margin: 0; padding: 0; }
  html, body { width: 1200px; height: 852px; overflow: hidden; }
  body {
    background: var(--backdrop);
    display: flex;
    align-items: center;
    justify-content: center;
    gap: 36px;
    font-family: "Open Sans", Arial, sans-serif;
  }
  .card {
    position: relative;
    width: 548px;
    height: 313px;
    border-radius: 14px;
    background: linear-gradient(135deg, var(--card-edge), var(--card) 60%);
    overflow: hidden;
    box-shadow: 0 14px 30px rgba(0,0,0,0.45);
  }

  /* front */
  .front-decor {
    position: absolute;
    left: 70px; top: -60px;
    width: 420px; height: 420px;
    border-radius: 50%;
    background: var(--faint);
  }
  .front-brand {
    position: absolute;
    left: 0; right: 0; top: 108px;
    display: flex;
    align-items: center;
    justify-content: center;
    gap: 14px;
  }
  .brand-dot {
    width: 34px; height: 34px;
    border-radius: 50%;
    background: var(--blue-bright);
    flex: none;
  }
  .brand-name {
    font-family: "Cinzel", Georgia, serif;
    font-weight: 600;
    font-size: 38px;
    letter-spacing: 2px;
    color: var(--ink);
    white-space: nowrap;
  }
  .tagline {
    position: absolute;
    left: 0; right: 0; top: 196px;
    text-align: center;
    font-family: "Cinzel", Georgia, serif;
    font-size: 17px;
    letter-spacing: 2.5px;
    color: var(--ink);
  }

  /* back */
  .back-emblem {
    position: absolute;
    left: 40px; top: 40px;
    width: 250px; height: 250px;
    border-radius: 50%;
    background: linear-gradient(160deg, var(--blue-bright), var(--blue));
  }
  .back-decor {
    position: absolute;
    right: -60px; top: -80px;
    width: 300px; height: 300px;
    border-radius: 50%;
    background: var(--faint);
  }
  .contact {
    position: absolute;
    left: 310px; top: 38px;
    color: var(--ink);
    font-size: 12.5px;
    line-height: 1.45;
  }
  .person-name {
    font-weight: 700;
    font-size: 14px;
    color: var(--blue-light);
    letter-spacing: 0.5px;
  }
  .person-title { font-size: 11px; color: var(--silver); margin-bottom: 12px; }
  .address { margin-bottom: 12px; }
  .contact-row { display: flex; align-items: center; gap: 9px; }
  .contact-row svg { width: 12px; height: 12px; fill: var(--silver); flex: none; }
  .social {
    display: flex;
    gap: 8px;
    margin-top: 10px;
    margin-left: 21px;
  }
  .social-item {
    display: flex;
    align-items: center;
    gap: 4px;
    font-size: 10px;
    color: var(--blue-light);
  }
  .social-item span.sq {
    width: 10px; height: 10px;
    border-radius: 2px;
    background: var(--blue-light);
  }
</style>
</head>
<body>

<section class="card card-front" aria-label="Card front">
  <div class="front-decor" role="img" aria-label="Faint large brand mark decoration"></div>
  <div class="front-brand">
    <span class="brand-dot"></span>
    <span class="brand-name">LARKSPUR TALENT</span>
  </div>
  <p class="tagline">READY FOR WHAT COMES NEXT</p>
</section>

<section class="card card-back" aria-label="Card back">
  <div class="back-decor" role="img" aria-label="Faint brand mark decoration"></div>
  <div class="back-emblem" role="img" aria-label="Large blue brand emblem"></div>
  <div class="contact">
    <p class="person-name">DANA WHITCOMBE</p>
    <p class="person-title">CEO</p>
    <p class="address">2140 W Larkin Ave, Suite 310<br>Brightwater, NV 89012, USA</p>
    <p class="contact-row">
      <svg viewBox="0 0 12 12"><path d="M2 1h2.5l1 3-1.5 1a6 6 0 0 0 3 3l1-1.5 3 1V11c-5 0-9-4-9-9z"/></svg>
      555| 201-0148
    </p>
    <p class="contact-row">
      <svg viewBox="0 0 12 12"><rect x="3" y="1" width="6" height="3"/><rect x="1" y="5" width="10" height="4" rx="1"/><rect x="3" y="8" width="6" height="3"/></svg>
      555| 201-0193
    </p>
    <p class="contact-row">
      <svg viewBox="0 0 12 12"><path d="M1 3h10v7H1z M1 3l5 4 5-4" stroke="#111214" stroke-width="0.8"/></svg>
      dana@larkspurtalent.example
    </p>
    <p class="contact-row">
      <svg viewBox="0 0 12 12"><circle cx="6" cy="6" r="5"/><path d="M1 6h10M6 1v10" stroke="#111214" stroke-width="0.8"/></svg>
      www.larkspurtalent.example
    </p>
    <div class="social">
      <span class="social-item"><span class="sq"></span>Blipster</span>
      <span class="social-item"><span class="sq"></span>Careerloop</span>
      <span class="social-item"><span class="sq"></span>Myriada</span>
    </div>
  </div>
</section>

</body>
</html>
```